Business Card for beauty technology startup

Design Glimora Business Card for a Beauty, based on the website identity and colors (https://www.glimora-example.com).
Glimora is a beauty tech startup that gathers helpful product info for beauty lovers and consumers (such as availability on stores, price range and product reviews) for makeup products. The card design must be young, colorful but clean, and very modern.

Target Market(s)

woman, 15-35

Industry/Entity Type

Cosmetics

Contact Information for Business Card

Full Name, address, phone

Font styles to use
Other font styles liked:
• Advent Pro

Colors
e34297
86cfc6
ffffff
5c5c5c
e8e8e8
e667a6
b2b2b2

Requirements
Must have
• One full colored side with a creative design and another with card info
• Use Color palette: #95C5C5 and/or #D38AA5
• Use fonts: Advent Pro
• Use website identity: https://www.glimora-example.com
Nice to have
• If needed extra font: Roboto

```html
<!DOCTYPE html>
<html lang="en">
<head>
<meta charset="utf-8">
<title>Glimora Business Card</title>
<link rel="stylesheet" href="https://fonts.googleapis.com/css2?family=Advent+Pro:wght@300;400&family=Montserrat:wght@400&family=Roboto:wght@400;500&display=swap">
<style>
  :root {
    --bg: #e8e8e8;
    --teal: #95c5c5;
    --white: #ffffff;
    --plum: #45313b;
    --rose: #b87a96;
    --rose-tab: #c98aa6;
    --ink: #4a3c43;
    --rule: #6b5a62;
  }
  * { margin: 0; padding: 0; box-sizing: border-box; }
  html, body { width: 1200px; height: 1155px; overflow: hidden; background: var(--bg); }
  .stage { position: relative; width: 1200px; height: 1155px; }

  .card {
    position: absolute;
    left: 218px;
    width: 758px;
    height: 434px;
    border-radius: 29px;
    overflow: hidden;
    box-shadow: 0 4px 8px rgba(0,0,0,0.22);
  }
  .card--front { top: 134px; background: var(--teal); }
  .card--back  { top: 596px; background: var(--white); }

  .ring { position: absolute; left: 0; top: 0; width: 758px; height: 434px; }

  .brand-dot {
    position: absolute;
    left: 54px; top: 46px;
    width: 100px; height: 100px;
    border: 2px solid var(--white);
    border-radius: 50%;
  }
  .brand-name {
    position: absolute;
    font-family: "Advent Pro", sans-serif;
    font-weight: 300;
    letter-spacing: 0.14em;
    line-height: 1;
  }
  .card--front .brand-name { left: 192px; top: 58px; font-size: 72px; color: var(--white); }
  .card--back  .brand-name { left: 36px; top: 42px; font-size: 82px; color: var(--plum); }

  .name-tab {
    position: absolute; left: -6px; top: 228px;
    width: 14px; height: 52px;
    border-radius: 5px;
    background: var(--rose-tab);
  }
  .person-name {
    position: absolute; left: 36px; top: 234px;
    font-family: "Roboto", sans-serif; font-weight: 500;
    font-size: 25px; line-height: 1; letter-spacing: 0.02em;
    color: var(--rose);
  }
  .person-role {
    position: absolute; left: 36px; top: 264px;
    font-family: "Roboto", sans-serif; font-weight: 400;
    font-size: 16px; line-height: 1; letter-spacing: 0.03em;
    color: var(--ink);
  }
  .rule {
    position: absolute; left: 36px; top: 303px;
    width: 682px; height: 1px; background: var(--rule);
  }
  .contact-list { position: absolute; left: 36px; top: 326px; list-style: none; }
  .contact-item {
    display: flex; align-items: center;
    height: 28.5px;
    font-family: "Montserrat", sans-serif; font-size: 19px;
    color: var(--ink); letter-spacing: 0.02em;
  }
  .contact-icon { width: 12px; height: 12px; margin-right: 20px; margin-left: 2px; }
  .address {
    position: absolute; right: 40px; top: 355px;
    text-align: right;
    font-family: "Montserrat", sans-serif; font-size: 19px;
    line-height: 28.5px; color: var(--ink); letter-spacing: 0.02em;
  }
</style>
</head>
<body>
<main class="stage">

  <section class="card card--front" aria-label="Card front">
    <svg class="ring" viewBox="0 0 758 434" aria-hidden="true">
      <circle cx="582" cy="448" r="192" fill="none" stroke="var(--plum)" stroke-width="6.5"/>
    </svg>
    <span class="brand-dot" aria-hidden="true"></span>
    <h1 class="brand-name">GLIMORA</h1>
  </section>

  <section class="card card--back" aria-label="Card back">
    <svg class="ring" viewBox="0 0 758 434" aria-hidden="true">
      <circle cx="582" cy="-14" r="192" fill="none" stroke="var(--plum)" stroke-width="6.5"/>
    </svg>
    <h2 class="brand-name">GLIMORA</h2>

    <span class="name-tab" aria-hidden="true"></span>
    <p class="person-name">DANA FELIKS</p>
    <p class="person-role">OWNER</p>
    <div class="rule"></div>

    <ul class="contact-list">
      <li class="contact-item">
        <svg class="contact-icon" viewBox="0 0 12 12" aria-hidden="true"><path d="M3 1 L5 1 L5 3.5 L4 4.5 Q5 7 7.5 8 L8.5 7 L11 7 L11 9 Q10 11 8 11 Q2 10 1 4 Q1 2 3 1Z" fill="var(--rose)"/></svg>
        555.014.2290
      </li>
      <li class="contact-item">
        <svg class="contact-icon" viewBox="0 0 12 12" aria-hidden="true"><rect x="1" y="2.5" width="10" height="7" fill="none" stroke="var(--rose)" stroke-width="1.2"/><path d="M1 3 L6 7 L11 3" fill="none" stroke="var(--rose)" stroke-width="1.2"/></svg>
        hello@glimora-example.com
      </li>
      <li class="contact-item">
        <svg class="contact-icon" viewBox="0 0 12 12" aria-hidden="true"><circle cx="6" cy="6" r="5" fill="none" stroke="var(--rose)" stroke-width="1.2"/><path d="M1 6 H11 M6 1 Q3 6 6 11 M6 1 Q9 6 6 11" fill="none" stroke="var(--rose)" stroke-width="1"/></svg>
        www.glimora-example.com
      </li>
    </ul>

    <address class="address" style="font-style: normal;">
      48 Palm Row<br>
      Harbor City, FL 30000
    </address>
  </section>

</main>
</body>
</html>
```